9x12 Business Brochure, 3 fold, for Internet Marketing Company

I'd like to have a brochure designed for my Internet marketing company. I have the content all ready, 10 Internet Marketing Myths, which you can see here: http://www.brisklanternstudio.example/usual-web-promotion-fables/. I'm looking for something creative and business to business. The company is all about Internet marketing. I like the "http://" header I use at our website. People like it too and identify with it. Audience is business owners 35 to 55 years old. I use blue at my website. I *think* I would like the cover page (front page) to open with some attention grabbing text, that basically takes most of the front page of the brochure. It would probably say: "I Can Help You Get BETTER RESULTS from Your Website, More Traffic, TOP RANKINGS at Quorble, More Leads and MORE SALES. But first you'll have to avoid these common Internet marketing myths..." The inside pages would have the content from above (the 10 myths). The back page would have testimonials that I can provide. And the inside folded in page (or what I call the inside folded in page) would have a list of services. I think I want the dimensions 12x9 which is a larger sized, three-fold brochure.

Target Market(s)

I use this brochure to send to business owners and managers to show them I know what I'm talking about and and expert. See attachment for content.

Industry/Entity Type

Marketing

Requirements
Should not have
• No clipart. Probably not illustrations. Photos. The "http://" used at the site is something people "connect" with and get that this is about Internet marketing.

```html
<!DOCTYPE html>
<html lang="en">
<head>
<meta charset="utf-8">
<title>Dana Whitcombe Consulting – Tri-fold Brochure Outside</title>
<link rel="stylesheet" href="https://fonts.googleapis.com/css2?family=Arimo:wght@700&family=Carlito:ital,wght@0,400;0,700;1,400&family=Roboto+Condensed:wght@700&display=swap">
<style>
  :root {
    --brand-blue: #4a86b8;
    --band-blue: #3f7fbf;
    --stripe-dark: #3a3a3a;
    --ink: #1c1c1c;
    --body-ink: #2a2a2a;
    --link-blue: #2f7dc2;
    --muted: #4a4a4a;
    --paper: #ffffff;
    --quote-band: #3b3b3b;
  }
  * { box-sizing: border-box; margin: 0; padding: 0; }
  html, body { width: 1200px; height: 924px; overflow: hidden; background: var(--paper); }
  .brochure { position: relative; width: 1200px; height: 924px; display: flex; }
  .panel { position: relative; width: 400px; height: 924px; overflow: hidden; }

  .section-band { position: absolute; left: 0; top: 33px; height: 45px; }
  .section-band h2 {
    position: absolute; left: 28px; top: 0; line-height: 45px;
    font-family: "Roboto Condensed", "Arial Narrow", sans-serif;
    font-weight: 700; font-size: 26px; color: #fff; letter-spacing: .3px; white-space: nowrap;
  }

  /* Services panel */
  .services { background: linear-gradient(180deg, #f4f6f8 0%, #e3ebf3 45%, #c9dcee 100%); }
  .services .backdrop {
    position: absolute; left: 0; top: 230px; width: 400px; height: 600px;
    background: radial-gradient(ellipse at 40% 55%, rgba(150,185,225,.55) 0%, rgba(190,212,236,.3) 45%, rgba(255,255,255,0) 75%);
  }
  .service-list { position: absolute; left: 28px; top: 111px; list-style: none; }
  .service-list li {
    position: relative; padding-left: 30px; height: 33.3px; line-height: 33.3px;
    font-family: "Arimo", Arial, sans-serif; font-weight: 700; font-size: 17.5px; color: var(--ink);
    white-space: nowrap;
  }
  .service-list li::before {
    content: ""; position: absolute; left: 0; top: 11px; width: 13px; height: 13px; border-radius: 50%;
    background: radial-gradient(circle at 35% 35%, #8a8a8a, #3a3a3a 70%);
  }
  .quote-band {
    position: absolute; left: 0; top: 833px; width: 400px; height: 57px; background: var(--quote-band);
    display: flex; align-items: center; justify-content: center; text-align: center;
    font-family: "Carlito", Calibri, sans-serif; font-style: italic; font-size: 18px; line-height: 1.15; color: #fff;
  }

  /* Success stories panel */
  .stories { background: var(--paper); border-right: 1px solid #e6e6e6; }
  .stories .sparkle {
    position: absolute; left: 0; top: 780px; width: 400px; height: 144px;
    background: radial-gradient(ellipse at 50% 80%, rgba(176,205,235,.55) 0%, rgba(255,255,255,0) 70%);
  }
  .testimonials { position: absolute; left: 28px; top: 108px; width: 346px; }
  .testimonial {
    font-family: "Carlito", Calibri, sans-serif; font-size: 12.4px; line-height: 1.2; color: var(--body-ink);
    text-align: justify; margin-bottom: 14px;
  }
  .testimonial .topic { font-size: 16.5px; color: var(--link-blue); margin-right: 3px; }
  .contact { position: absolute; left: 0; top: 818px; width: 400px; text-align: center; }
  .contact .name { font-family: "Arimo", Arial, sans-serif; font-weight: 700; font-size: 21px; color: var(--link-blue); }
  .contact .email { font-family: "Arimo", Arial, sans-serif; font-weight: 700; font-size: 14px; color: var(--ink); margin-top: 9px; }
  .contact .phone { font-family: "Roboto Condensed", "Arial Narrow", sans-serif; font-weight: 700; font-size: 20px; color: var(--muted); margin-top: 6px; }

  /* Front cover */
  .cover { background: var(--brand-blue); color: #fff; font-family: "Carlito", Calibri, sans-serif; }
  .cover .map-tint {
    position: absolute; left: 150px; top: 720px; width: 250px; height: 180px;
    background: radial-gradient(ellipse at 50% 50%, rgba(40,90,140,.35) 0%, rgba(74,134,184,0) 70%);
  }
  .cover .headline { position: absolute; left: 30px; top: 40px; font-size: 56px; font-weight: 400; line-height: 1; }
  .pitch { position: absolute; left: 30px; top: 130px; font-size: 35px; line-height: 47px; }
  .pitch .caps { text-transform: uppercase; }
  .cover .teaser { position: absolute; left: 33px; top: 688px; font-style: italic; font-size: 18.5px; line-height: 1.3; }
  .cover .company {
    position: absolute; left: 33px; top: 808px;
    font-family: "Roboto Condensed", "Arial Narrow", sans-serif; font-weight: 700; font-size: 27px; color: #0f1a24;
  }
  .cover .phone {
    position: absolute; left: 33px; top: 842px;
    font-family: "Roboto Condensed", "Arial Narrow", sans-serif; font-weight: 700; font-size: 48px; color: #0f1a24;
  }
</style>
</head>
<body>
<main class="brochure">

  <section class="panel services">
    <div class="backdrop" role="img" aria-label="Soft blue abstract backdrop of translucent web page tiles"></div>
    <div class="section-band">
      <svg width="350" height="45" viewBox="0 0 350 45" aria-hidden="true">
        <polygon points="0,0 296,0 323,45 0,45" fill="var(--band-blue)"/>
        <polygon points="306,0 321,0 348,45 333,45" fill="var(--stripe-dark)"/>
      </svg>
      <h2>SERVICES &amp; EXPERTISE</h2>
    </div>
    <ul class="service-list">
      <li>Internet Strategy Development</li>
      <li>Website Reviews</li>
      <li>Website "Overhauls"</li>
      <li>Custom Website Design</li>
      <li>Blog Design &amp; Support</li>
      <li>Online Marketing Copywriting</li>
      <li>Social Media Marketing</li>
      <li>Search Engine Optimization (SEO)</li>
      <li>Conversion Optimization</li>
      <li>Engagement Marketing Management</li>
      <li>Using Friendloop for Business</li>
      <li>Quorble+, Clipstream, Pinboardly</li>
      <li>Email Marketing &amp; Production</li>
      <li>Inquiry and Lead Development</li>
      <li>Quorble Bidwords Pay-Per-Click</li>
      <li>Quorble Local Places (maps)</li>
      <li>E-Commerce Development</li>
      <li>High-Performance Hosting</li>
      <li>Security &amp; Contingency Planning</li>
      <li>One-on-One or Group Training</li>
    </ul>
    <blockquote class="quote-band">“If you think it’s expensive to hire an expert,<br>wait until you hire an amateur.”</blockquote>
  </section>

  <section class="panel stories">
    <div class="sparkle" role="img" aria-label="Faint blue sparkle texture"></div>
    <div class="section-band">
      <svg width="300" height="45" viewBox="0 0 300 45" aria-hidden="true">
        <polygon points="0,0 248,0 275,45 0,45" fill="var(--band-blue)"/>
        <polygon points="258,0 273,0 300,45 285,45" fill="var(--stripe-dark)"/>
      </svg>
      <h2>SUCCESS STORIES</h2>
    </div>
    <div class="testimonials">
      <p class="testimonial"><span class="topic">Quorble Rankings:</span> “... we have spent over a year trying to get onto page one at Quorble. It has been very frustrating and we’ve wasted a lot of time and money. Dana explained everything very clearly and we did everything she told us. 90 days later we’re now showing up on the first page of Quorble!”</p>
      <p class="testimonial"><span class="topic">Website Design:</span> “We needed a new website that properly reflected our company and the products and services we sell. We started getting more leads within 72 hours of launching the new site Dana and her team designed for us. We’re also getting better results from our Quorble Bidwords pay-per-click advertising and more of those clicks are turning into inquiries!”</p>
      <p class="testimonial"><span class="topic">Traffic Building:</span> “We’ve seen a 45% increase in our monthly traffic over the last 90 days. Our daily visits are consistently increasing and our average bounce rate is down by 45%. Thanks Dana!”</p>
      <p class="testimonial"><span class="topic">More Leads:</span> “The leads we get from our website have increased dramatically. This past month (February) was the best month ever for new leads directly from our website. We made a great investment hiring you, thanks Dana.”</p>
      <p class="testimonial"><span class="topic">Social Media:</span> “Your social media strategy has changed everything for us. Our Friendloop “Likes” jumped 180% last month and referral traffic from Friendloop is up more than 300% from 90 days ago. Finally, social media is working for us like it should.”</p>
      <p class="testimonial"><span class="topic">Blogging:</span> “We implemented the blogging strategy you developed for us and it’s paying off already. Traffic is up and inquiries are up. Thanks Dana!”</p>
      <p class="testimonial"><span class="topic">Website Overhaul:</span> “Our new website started generating more leads within days of going LIVE. And now with the site in PressLeaf, we can do the edits we always wanted to but had to pay a designer/programmer to complete. It looks like we’ll double our business from last year thanks to the new site. Thanks a million (maybe literally!) Dana!”</p>
    </div>
    <address class="contact" style="font-style:normal">
      <div class="name">Dana Whitcombe</div>
      <div class="email">dana@whitcombeconsulting.example</div>
      <div class="phone">(555) 014-2290</div>
    </address>
  </section>

  <section class="panel cover">
    <div class="map-tint" role="img" aria-label="Faint darker blue map silhouette"></div>
    <h1 class="headline">I Can Help You</h1>
    <p class="pitch">
      <span class="caps">Get better results</span><br>
      from Your Website,<br>
      More Traffic,<br>
      <span class="caps">Top rankings</span><br>
      with Quorble, More<br>
      Inquiries, and<br>
      <span class="caps">More sales</span>
    </p>
    <p class="teaser">But first you’ll need to avoid these<br>Common Internet Marketing Myths...</p>
    <div class="company">DANA WHITCOMBE CONSULTING</div>
    <div class="phone">(555) 014-2290</div>
  </section>

</main>
</body>
</html>
```